Wine Radio Show web re-design

We need new website look for an unconventional, nationally-syndicated WINE RADIO show. Show is fun, hip, witty and covers all wine lifestyle topics. We are redesigning logo and looking for a redesign of our wordpress site that hosts all our audio podcasts, and the site design needs to leverage and maximize these podcasts. Do NOT use the logo currently on the website. The site is velvetcorkhour.net, please see more info on the attached.

Do NOT use the logo currently on the website. Please just typeset the name "Velvet Cork Hour".
Updates

Please do NOT use the logo from the current website. Please just use type (to match theme/deisgn) "Velvet Cork Hour". Thank you.

Hello Designers, Thank you for working on this project. A piece of feedback overall is that we'd like much less image/masthead space in general (the photos and images at the top). We'd like the navigation and the latest Velvet Cork podcast to be above the fold. Most of the wine imagery/scenery shots can be minimalized/drastically reduced/eliminated, to allow more room for the different sections. Hope that makes sense, and again, thank you for working on this!! Marta

Target Market(s)

Wine lovers and wine industry professionals, probably 30+ years old

Industry/Entity Type

Radio

Font styles to use
Serif
Sans Serif
Decorative
Other font styles liked:
• Modern retro fonts

Requirements
Must have
• Must keep current content of site:
http://velvetcorkhourshow.net/podcast/
Feature podcasts prominently.
Do NOT use the logo currently on the website.
Nice to have
• Graphics to consider incorporating:
• WINE: Grapes, wine glasses, wine bottles, wine pouring, corkscrews, grapevines, vineyards
• RADIO symbols: soundwaves, antenna, radio icon, Podcast symbols, microphone
Should not have
• Do NOT use current logo - just use type.

```html
<!DOCTYPE html>
<html lang="en">
<head>
<meta charset="utf-8">
<title>Velvet Cork Hour</title>
<link href="https://fonts.googleapis.com/css2?family=Arimo:wght@700&family=Open+Sans:ital,wght@0,400;0,600;0,700;1,400;1,600&family=Rye&display=swap" rel="stylesheet">
<style>
:root{
  --wood-dark:#24150c;
  --wood:#3b2516;
  --wood-light:#5a3a22;
  --panel:#2b2b2b;
  --column:#1f1f1f;
  --red:#b3121a;
  --green:#9ccc2e;
  --text:#a9a9a9;
  --muted:#7b7b7b;
  --white:#ffffff;
  --nav-active:#44506a;
}
*{box-sizing:border-box;margin:0;padding:0}
html,body{width:1200px;height:3163px;overflow:hidden}
body{
  position:relative;
  font-family:"Open Sans",Arial,sans-serif;
  color:var(--text);
  background:
    repeating-linear-gradient(90deg,rgba(0,0,0,.18) 0 3px,transparent 3px 58px,rgba(255,255,255,.03) 58px 61px,transparent 61px 120px),
    linear-gradient(180deg,var(--wood-light),var(--wood) 40%,var(--wood-dark));
}
.abs{position:absolute}

/* header */
.vine-left{left:0;top:0;width:170px;height:200px;background:radial-gradient(circle at 45% 55%,#5a3d6e,#3a2444 60%,transparent 72%)}
.vine-right{right:0;top:0;width:170px;height:200px;background:radial-gradient(circle at 55% 55%,#b8c85a,#7f9a2e 60%,transparent 72%)}
.top-links{top:28px;left:365px;display:flex;gap:46px;font-size:14px}
.top-links a{color:var(--green);text-decoration:none}
.top-links a+a{color:var(--white)}
.site-title{left:190px;top:138px;font-family:"Arimo",Arial,sans-serif;font-weight:700;font-size:44px;line-height:1;color:var(--white);letter-spacing:-.5px;white-space:nowrap}
.listen-live{left:833px;top:84px;width:169px;height:53px;background:rgba(15,10,6,.75);border-radius:4px;display:flex;align-items:center;gap:10px;padding-left:12px;text-decoration:none}
.listen-live .t{color:var(--green);font-weight:700;font-size:15px;line-height:1.05}
.listen-live .t small{display:block;font-size:10px;font-weight:600}
.search{left:812px;top:158px;width:211px;height:32px;background:#2a1008;border:1px solid #4a1d12;border-radius:3px;display:flex;align-items:center;justify-content:space-between;padding:0 10px;font-size:12px;color:#a3473a;font-style:italic}

/* nav */
.main-nav{top:232px;left:0;width:1200px;height:53px;background:linear-gradient(180deg,#d52a30,var(--red) 50%,#8a0c12);border-top:1px solid #e8555a;border-bottom:2px solid #5a0709;display:flex;padding-left:128px}
.main-nav a{color:var(--white);text-decoration:none;font-size:16px;line-height:51px;padding:0 13px;white-space:nowrap}
.main-nav a.active{background:var(--nav-active)}

/* compact hero */
.hero{top:285px;left:0;width:1200px;height:190px;background:
  radial-gradient(ellipse at 15% 75%,#2d4a1a,transparent 45%),
  radial-gradient(ellipse at 80% 90%,#5c2330,transparent 40%),
  linear-gradient(180deg,#8ea36a 0%,#5e7a3e 40%,#7a6a48 75%,#5a4a32 100%)}
.hero-title{left:520px;top:345px;font-family:"Rye",serif;font-size:52px;color:#8e1419;line-height:1;white-space:nowrap}

/* content panel */
.panel{left:133px;top:475px;width:932px;height:2585px;background:var(--panel)}
.main-col{left:148px;top:492px;width:601px}
.video{height:320px;background:linear-gradient(180deg,#3a2c22,#1d1a17);border:2px solid #555;position:relative}
.video svg{position:absolute;left:260px;top:118px}
.section-head{height:40px;background:linear-gradient(180deg,#b8141c,#8a0c12);color:var(--white);font-size:19px;font-weight:600;line-height:40px;padding-left:14px;white-space:nowrap}
.main-col .section-head{margin-top:24px}
.post{height:530px;padding:18px 14px 0 14px;border-bottom:1px solid #3a3a3a;background:var(--column)}
.post h2{font-size:16px;font-weight:700;color:var(--green);line-height:24px}
.post .meta{font-size:11px;color:var(--muted);margin:2px 0 14px}
.post .meta b{color:var(--green);font-weight:600}
.post .lead{display:flex;gap:16px}
.post .thumb{flex:0 0 245px;height:160px;border:3px solid #ddd}
.post .lead p,.post .more{font-size:12.5px;line-height:22px;color:var(--muted)}
.post .more{margin-top:10px}
.actions{display:flex;gap:14px;margin-top:18px}
.btn{display:flex;align-items:center;gap:8px;background:#141414;color:var(--white);font-size:14px;font-weight:600;height:32px;padding:0 14px;border-radius:3px;white-space:nowrap}
.cats{font-size:11px;margin-top:16px;color:var(--muted)}
.cats b{color:var(--white);font-style:italic}
.like{display:flex;align-items:center;gap:10px;margin-top:12px;font-size:11px;font-style:italic;font-weight:600;color:var(--muted)}
.like span.box{width:44px;height:18px;background:#5a6fa0;border-radius:2px}

/* sidebar */
.side{left:772px;width:278px}
.show-list{background:var(--column);padding:8px 10px}
.show{display:flex;align-items:center;gap:10px;height:72px}
.show+.show{border-top:1px solid #333}
.date{display:flex;flex:0 0 78px;height:46px}
.date .day{width:38px;background:var(--red);color:var(--white);font-weight:700;font-size:17px;display:flex;align-items:center;justify-content:center}
.date.gray .day{background:#3b3b3b}
.date .mon{flex:1;background:#3a3a3a;color:var(--white);font-size:13px;font-style:italic;font-weight:600;line-height:17px;padding:6px 0 0 6px}
.date .mon small{display:block;font-size:10px}
.show p{font-size:12px;line-height:18px;color:var(--muted)}
.show p.hot{color:var(--green)}
.ads{top:1110px;height:1073px}
.ad{position:absolute}
.archive-list{background:var(--column)}
.archive-list li{list-style:none;height:38px;line-height:38px;padding-left:14px;font-size:12px;color:var(--muted);border-bottom:1px solid #2f2f2f}
.archive-list li.current{background:#333;color:var(--green)}

/* footer */
.footer{left:0;top:3060px;width:1200px;height:103px;background:rgba(15,9,5,.6)}
.foot-links{top:3090px;left:0;width:1200px;text-align:center;font-size:13px;color:var(--white)}
.foot-links a{color:var(--white);text-decoration:none}
.foot-links a:first-child{color:var(--green)}
.copy{top:3128px;left:133px;font-size:13px;color:#cfcfcf}
.social{top:3124px;left:855px;display:flex;gap:8px}
.social span{width:26px;height:26px;border-radius:50%;background:#4f6f9a}
</style>
</head>
<body>

<header>
  <div class="abs vine-left" role="img" aria-label="Bunch of purple grapes hanging from a vine"></div>
  <div class="abs vine-right" role="img" aria-label="Bunch of green grapes hanging from a vine"></div>
  <nav class="abs top-links"><a href="#">Find Shows/Bands</a><a href="#">Velvet Cork Hour</a></nav>
  <h1 class="abs site-title">Velvet Cork Hour</h1>
  <a class="abs listen-live" href="#">
    <svg width="30" height="30" viewBox="0 0 30 30"><circle cx="15" cy="15" r="14" fill="none" stroke="#9ccc2e" stroke-width="2"/><rect x="11" y="7" width="8" height="12" rx="4" fill="#9ccc2e"/><path d="M8 15a7 7 0 0 0 14 0M15 22v3" stroke="#9ccc2e" stroke-width="2" fill="none"/></svg>
    <span class="t">LISTEN LIVE<small>CLICK HERE</small></span>
  </a>
  <div class="abs search">Search...
    <svg width="16" height="16" viewBox="0 0 16 16"><circle cx="6.5" cy="6.5" r="5" fill="none" stroke="#c8a23a" stroke-width="2"/><path d="M10 10l5 5" stroke="#c8a23a" stroke-width="2"/></svg>
  </div>
</header>

<nav class="abs main-nav">
  <a class="active" href="#">Home</a><a href="#">Episode Archives</a><a href="#">Uncorked</a><a href="#">About the Show</a><a href="#">About the Host</a><a href="#">On the Air</a><a href="#">Blog</a><a href="#">Store</a><a href="#">Contact Us</a>
</nav>

<section class="abs hero" role="img" aria-label="Vineyard scene with a wine bottle, a glass of red wine and bunches of grapes on straw"></section>
<div class="abs hero-title">LOREM IPSUM DOLOR</div>

<div class="abs panel"></div>

<main class="abs main-col">
  <div class="video" role="img" aria-label="Featured episode video">
    <svg width="80" height="80" viewBox="0 0 80 80"><circle cx="40" cy="40" r="38" fill="#7a9a22"/><path d="M31 24l26 16-26 16z" fill="#1f1f1f"/></svg>
  </div>
  <div class="section-head">Velvet Cork</div>

  <article class="post">
    <h2>Episode #250 – The Manipulation of Wine</h2>
    <div class="meta">Posted on May 10, 2014 by <b>Velvet Cork</b></div>
    <div class="lead"><div class="thumb" role="img" aria-label="Table of wine bottles and gift boxes" style="background:linear-gradient(180deg,#c9ccd0,#8d9094)"></div>
      <p>Daniel Reyes is beginning to get terribly bored with wine. He hasn't lost his passion for a good bottle of wine. But, rather, he has become impatient with finding decent bottles of wine at a decent price. Your Velvet Cork host believes that wines are beginning to taste more and more alike. Why is that? Manipulation</p></div>
    <p class="more">This week, respected wine educator, wine judge and Ridgeback Hollow Vineyards winemaker Leo Marsh joins the conversation to explain why he feels that it is becoming more and more difficult to zero in on wines that he'd like to recommend to you. He talks about overcoming 'sameness in the Golden Age of wine</p>
    <div class="actions">
      <span class="btn"><svg width="14" height="14" viewBox="0 0 14 14"><rect x="4" y="1" width="6" height="8" rx="3" fill="#fff"/><path d="M2 7a5 5 0 0 0 10 0M7 12v2" stroke="#fff" stroke-width="1.5" fill="none"/></svg>Listen live</span>
      <span class="btn"><svg width="14" height="14" viewBox="0 0 14 14"><path d="M7 1v8M3 6l4 4 4-4M2 13h10" stroke="#fff" stroke-width="2" fill="none"/></svg>Download</span>
    </div>
    <div class="cats"><b>Categories :</b> Episode Archives</div>
    <div class="like"><span class="box"></span>Be the first of your friends to like this.</div>
  </article>

  <article class="post">
    <h2>Episode #251 – The Largest Fine Wine Region on the Planet is Spelled: Bordeaux!</h2>
    <div class="meta">Posted on May 10, 2014 by <b>Velvet Cork</b></div>
    <div class="lead"><div class="thumb" role="img" aria-label="Table of wine bottles and gift boxes" style="background:linear-gradient(180deg,#c9ccd0,#8d9094)"></div>
      <p>Daniel Reyes is beginning to get terribly bored with wine. He hasn't lost his passion for a good bottle of wine. But, rather, he has become impatient with finding decent bottles of wine at a decent price. Your Velvet Cork host believes that wines are beginning to taste more and more alike. Why is that? Manipulation</p></div>
    <p class="more">This week, respected wine educator, wine judge and Ridgeback Hollow Vineyards winemaker Leo Marsh joins the conversation to explain why he feels that it is becoming This week, respected wine educator, wine judge and Ridgeback</p>
    <div class="actions">
      <span class="btn"><svg width="14" height="14" viewBox="0 0 14 14"><rect x="4" y="1" width="6" height="8" rx="3" fill="#fff"/><path d="M2 7a5 5 0 0 0 10 0M7 12v2" stroke="#fff" stroke-width="1.5" fill="none"/></svg>Listen live</span>
      <span class="btn"><svg width="14" height="14" viewBox="0 0 14 14"><path d="M7 1v8M3 6l4 4 4-4M2 13h10" stroke="#fff" stroke-width="2" fill="none"/></svg>Download</span>
    </div>
    <div class="cats"><b>Categories :</b> Episode Archives</div>
    <div class="like"><span class="box"></span>Be the first of your friends to like this.</div>
  </article>

  <article class="post">
    <h2>Episode #252 – The Inside Scoop on China's Extraordinary Growth and Passion for Wine</h2>
    <div class="meta">Posted on May 10, 2014 by <b>Velvet Cork</b></div>
    <div class="lead"><div class="thumb" role="img" aria-label="Wine barrel, grapes and bottles in a cellar" style="background:linear-gradient(135deg,#5a3a22,#1e140d)"></div>
      <p>Daniel Reyes is beginning to get terribly bored with wine. He hasn't lost his passion for a good bottle of wine. But, rather, he has become impatient with finding decent bottles of wine at a decent price. Your Velvet Cork host believes that wines are beginning to taste more and more alike. Why is that? Manipulation</p></div>
    <p class="more">This week, respected wine educator, wine judge and Ridgeback Hollow Vineyards winemaker Leo Marsh joins the conversation to explain why he feels that it is becoming more and more difficult to zero in on wines that he'd like to recommend to you</p>
    <div class="actions">
      <span class="btn"><svg width="14" height="14" viewBox="0 0 14 14"><rect x="4" y="1" width="6" height="8" rx="3" fill="#fff"/><path d="M2 7a5 5 0 0 0 10 0M7 12v2" stroke="#fff" stroke-width="1.5" fill="none"/></svg>Listen live</span>
      <span class="btn"><svg width="14" height="14" viewBox="0 0 14 14"><path d="M7 1v8M3 6l4 4 4-4M2 13h10" stroke="#fff" stroke-width="2" fill="none"/></svg>Download</span>
    </div>
    <div class="cats"><b>Categories :</b> Episode Archives</div>
    <div class="like"><span class="box"></span>Be the first of your friends to like this.</div>
  </article>

  <article class="post">
    <h2>Episode #253 – Knowing Wine From Lark: The Expert Storyteller at Cellarline.com</h2>
    <div class="meta">Posted on May 10, 2014 by <b>Velvet Cork</b></div>
    <div class="lead"><div class="thumb" role="img" aria-label="Glasses of red wine in a row" style="background:linear-gradient(135deg,#7a1820,#2a0a0c)"></div>
      <p>Daniel Reyes is beginning to get terribly bored with wine. He hasn't lost his passion for a good bottle of wine. But, rather, he has become impatient with finding decent bottles of wine at a decent price. Your Velvet Cork host believes that wines are beginning to taste more and more alike. Why is that? Manipulation</p></div>
    <p class="more">This week, respected wine educator, wine judge and Ridgeback Hollow Vineyards winemaker Leo Marsh joins the conversation to explain why he feels that it is becoming more and more difficult to zero in on wines that he'd like to recommend to yo</p>
    <div class="actions">
      <span class="btn"><svg width="14" height="14" viewBox="0 0 14 14"><rect x="4" y="1" width="6" height="8" rx="3" fill="#fff"/><path d="M2 7a5 5 0 0 0 10 0M7 12v2" stroke="#fff" stroke-width="1.5" fill="none"/></svg>Listen live</span>
      <span class="btn"><svg width="14" height="14" viewBox="0 0 14 14"><path d="M7 1v8M3 6l4 4 4-4M2 13h10" stroke="#fff" stroke-width="2" fill="none"/></svg>Download</span>
    </div>
    <div class="cats"><b>Categories :</b> Episode Archives</div>
    <div class="like"><span class="box"></span>Be the first of your friends to like this.</div>
  </article>
</main>

<aside class="abs side" style="top:492px">
  <div class="section-head">Recent Shows</div>
  <div class="show-list">
    <div class="show"><div class="date"><span class="day">31</span><span class="mon">May<small>2014</small></span></div><p class="hot">Episode #253 – Knowing Wine From Lark: The Expert Storyteller at</p></div>
    <div class="show"><div class="date gray"><span class="day">24</span><span class="mon">May<small>2014</small></span></div><p>Episode #252 – The Inside Scoop on China's Extraordinary Growth</p></div>
    <div class="show"><div class="date gray"><span class="day">17</span><span class="mon">May<small>2014</small></span></div><p>Episode #251 – The Largest Fine Wine Region on the Planet is Spelled:</p></div>
  </div>
</aside>

<aside class="abs side" style="top:793px">
  <div class="section-head">Uncorked</div>
  <div class="show-list">
    <div class="show"><div class="date"><span class="day">31</span><span class="mon">May<small>2014</small></span></div><p class="hot">Uncorked #625 – A Rather Unhappy Customer</p></div>
    <div class="show"><div class="date gray"><span class="day">24</span><span class="mon">May<small>2014</small></span></div><p>Uncorked #624 – The Culture of Wine is Popular</p></div>
    <div class="show"><div class="date gray"><span class="day">17</span><span class="mon">May<small>2014</small></span></div><p>Uncorked #623 – A National Treasure</p></div>
  </div>
</aside>

<aside class="abs side ads">
  <div class="ad" role="img" aria-label="Advertisement for a wine region guide book" style="left:0;top:0;width:136px;height:291px;background:linear-gradient(180deg,#efe3c3,#c9a86a)"></div>
  <div class="ad" role="img" aria-label="Advertisement for a wine country travel adventure" style="left:0;top:294px;width:136px;height:515px;background:linear-gradient(180deg,#e6d39a,#a57a2e 60%,#efe6cc)"></div>
  <div class="ad" role="img" aria-label="Advertisement showing where to listen on air" style="left:0;top:815px;width:136px;height:253px;background:linear-gradient(180deg,#f3f3f3,#d8d8d8)"></div>
  <div class="ad" role="img" aria-label="Advertisement to subscribe to the Uncorked podcast" style="left:142px;top:0;width:136px;height:69px;background:#f2f2f2"></div>
  <div class="ad" role="img" aria-label="Advertisement for a yard wine book" style="left:142px;top:73px;width:136px;height:383px;background:linear-gradient(180deg,#f7f4ea,#e0d8b8)"></div>
  <div class="ad" role="img" aria-label="Advertisement for cork cages and wine gadgets" style="left:142px;top:460px;width:136px;height:410px;background:linear-gradient(180deg,#fafafa,#cfc9bf)"></div>
  <div class="ad" role="img" aria-label="Advertisement for a wine tasting guru" style="left:142px;top:874px;width:136px;height:80px;background:#ececec"></div>
</aside>

<aside class="abs side" style="top:2200px">
  <div class="section-head">Archives</div>
  <ul class="archive-list">
    <li>May 2014</li><li class="current">April 2014</li><li>March 2014</li><li>February 2014</li><li>January 2014</li><li>December 2013</li><li>November 2013</li><li>October 2013</li><li>September 2013</li><li>August 2013</li><li>July 2013</li><li>June 2013</li>
  </ul>
</aside>

<footer>
  <div class="abs footer"></div>
  <nav class="abs foot-links"><a href="#">Home</a> &nbsp;/&nbsp; <a href="#">Velvet Cork Episode Archives</a> &nbsp;/&nbsp; <a href="#">About the Host</a> &nbsp;/&nbsp; <a href="#">About the Show</a> &nbsp;/&nbsp; <a href="#">Affiliate Stations</a> &nbsp;/&nbsp; <a href="#">Contact Us</a></nav>
  <p class="abs copy">© 2013 Velvet Cork Hour. All Rights Reserved.</p>
  <div class="abs social"><span></span><span></span><span></span><span></span><span></span><span></span><span></span></div>
</footer>

</body>
</html>
```